Varentoria Business Card and Letter Head

We are a leadership assessment consultancy based in Sydney, Australia. We help executive-level decison-makers select leaders for more senior level roles in corporate and government organisations. Our methodology is based on the latest research from the field of neuroscience.
We need a business card design and matching letter head that presents our company, Varentoria, as a:
1. trusted adviser to senior executive-level decison makers
2. niche consultancy who are experts in the field of assessing leadership talent
3. results-focused solution provider who balance scientific methods with pragmatic solutions
The following company details should be used in all designs:
Company Name: Varentoria
Details (for business card):
Derek Hanford
Prime Capacity Officer
Level 17, Marlow Tower
7 Marlow Square
Sydney, NSW 2011 Australia
Phone: 1300 582 714
Mobile: 0412 637 258
Email: derek.hanford@varentoria-example.com.au
Website: varentoria-example.com.au
I have attached the logo for Varentoria (for both a white and black background) - your business card and letter head designs must incoporate this logo and colour scheme.
Thanks for your interest in this project, I'm looking forward to receiving your ideas.
Regards,
Derek
Target Market(s)
Executive-level decison-makers in corporate and government organisations (e.g., CEO, VP, Head of Human Resources)
Industry/Entity Type
Leadership
Look and feel

```html
<!DOCTYPE html>
<html lang="en">
<head>
<meta charset="utf-8">
<title>Varentoria Business Card</title>
<link rel="stylesheet" href="https://fonts.googleapis.com/css2?family=Open+Sans:wght@300;400;700&display=swap">
<style>
  :root {
    --canvas: #e9e7e4;
    --card: #ffffff;
    --ink: #3d3d3f;
    --ink-soft: #5a5a5c;
    --muted: #8a8a8c;
    --accent: #c0281c;
  }
  * { box-sizing: border-box; margin: 0; padding: 0; }
  html, body {
    width: 1200px; height: 665px; overflow: hidden;
    background: var(--canvas);
    font-family: "Open Sans", Arial, sans-serif;
    color: var(--ink);
  }
  .stage {
    position: relative; width: 1200px; height: 665px;
    display: flex; align-items: center; justify-content: center; gap: 50px;
  }
  .card {
    position: relative; width: 540px; height: 320px;
    background: var(--card);
    box-shadow: 0 2px 10px rgba(0,0,0,0.12);
  }
  /* Front */
  .brand { position: absolute; left: 40px; top: 40px; }
  .brand-row { display: flex; align-items: center; gap: 14px; }
  .brand-mark { width: 26px; height: 26px; background: var(--ink); }
  .brand-name { font-weight: 700; font-size: 46px; letter-spacing: -1px; line-height: 1; color: var(--ink); }
  .tagline {
    margin-top: 6px; margin-left: 40px;
    font-weight: 300; font-size: 15.5px; letter-spacing: 0.5px;
    text-transform: uppercase; color: var(--muted);
  }
  .contact {
    position: absolute; right: 32px; top: 140px;
    list-style: none; text-align: right;
    font-size: 12.5px; line-height: 19px; color: var(--ink);
  }
  .contact li { display: flex; justify-content: flex-end; align-items: center; gap: 5px; }
  .contact svg { width: 11px; height: 11px; fill: var(--accent); flex: none; }
  .person { position: absolute; left: 40px; top: 222px; }
  .person-name { font-weight: 700; font-size: 15px; color: var(--accent); }
  .person-title { font-size: 12px; color: var(--ink-soft); margin-top: 2px; }
  .address { position: absolute; left: 40px; bottom: 26px; font-size: 12px; color: var(--ink-soft); }
  /* Back */
  .back { display: flex; flex-direction: column; align-items: center; justify-content: center; }
  .back .brand-row { gap: 16px; }
  .back .brand-mark { width: 40px; height: 40px; background: var(--accent); }
  .back .brand-name { font-size: 60px; }
  .web {
    margin-top: 42px; font-size: 16px; letter-spacing: 2.5px; color: var(--ink);
  }
  .web .domain { color: var(--accent); }
</style>
</head>
<body>
<main class="stage">
  <section class="card front">
    <div class="brand">
      <div class="brand-row">
        <span class="brand-mark"></span>
        <span class="brand-name">Varentoria</span>
      </div>
      <p class="tagline">Identifying Executive Ability</p>
    </div>

    <ul class="contact">
      <li><svg viewBox="0 0 12 12"><circle cx="6" cy="6" r="6"/><path d="M4 3.2l1 1.4-.6.7c.4.9 1 1.5 1.9 1.9l.7-.6 1.4 1-.5 1.1C5.6 8.5 3.5 6.4 3.3 4z" fill="#fff"/></svg>1300 582 714</li>
      <li><svg viewBox="0 0 12 12"><rect x="3" y="0.5" width="6" height="11" rx="1"/><rect x="4" y="2" width="4" height="5" fill="#fff"/></svg>0412 637 258</li>
      <li><svg viewBox="0 0 12 12"><rect x="0.5" y="2.5" width="11" height="7"/><path d="M1 3l5 3.5L11 3" stroke="#fff" stroke-width="1" fill="none"/></svg>derek.hanford@varentoria-example.com.au</li>
      <li><svg viewBox="0 0 12 12"><circle cx="6" cy="6" r="6"/><path d="M0.5 6h11M6 0.5c-2.5 3-2.5 8 0 11M6 0.5c2.5 3 2.5 8 0 11" stroke="#fff" stroke-width="0.8" fill="none"/></svg>www.varentoria-example.com.au</li>
    </ul>

    <div class="person">
      <p class="person-name">Derek Hanford</p>
      <p class="person-title">Prime Capacity Officer</p>
    </div>

    <p class="address">Level 17, Marlow Tower, 7 Marlow Square, Sydney, NSW 2011 Australia</p>
  </section>

  <section class="card back">
    <div class="brand-row">
      <span class="brand-mark"></span>
      <span class="brand-name">Varentoria</span>
    </div>
    <p class="web">www.<span class="domain">varentoria-example</span>.com.au</p>
  </section>
</main>
</body>
</html>
```